Business Card Design for Software Development Company

I am looking for a business card design the incorporates my new logo (attached below).

Key information to include:
Name: Martin Quelbrook
Title: CEO
Email: martin@brightwellcivic.example
Phone: 555-218-9403
Website: www.brightwellcivic.example

NOTE: This design should be easy to edit so that we can order cards for different members of our team.

```html
<!DOCTYPE html>
<html lang="en">
<head>
<meta charset="utf-8">
<title>Brightwell Labs Business Card</title>
<link href="https://fonts.googleapis.com/css2?family=Montserrat:wght@400;600;700&display=swap" rel="stylesheet">
<style>
  :root {
    --stage: #3b3b3d;
    --card-white: #ffffff;
    --navy: #2f3a52;
    --navy-card: #394158;
    --ink-light: #ffffff;
    --accent-orange: #ec7f27;
  }
  * { margin: 0; padding: 0; box-sizing: border-box; }
  html, body {
    width: 1200px;
    height: 1059px;
    overflow: hidden;
    background: var(--stage);
    font-family: "Montserrat", Arial, sans-serif;
  }
  .canvas { position: relative; width: 1200px; height: 1059px; }

  .card {
    position: absolute;
    left: 255px;
    width: 690px;
    height: 392px;
    border-radius: 20px;
    overflow: hidden;
  }
  .card-front { top: 100px; background: var(--card-white); color: var(--navy); }
  .card-back { top: 537px; background: var(--navy-card); color: var(--ink-light); }

  /* Front */
  .front-brand { position: absolute; left: 32px; top: 62px; }
  .brand-name {
    font-weight: 700;
    font-size: 40px;
    letter-spacing: -0.5px;
    line-height: 1;
  }
  .brand-tagline {
    margin-top: 6px;
    font-weight: 600;
    font-size: 6px;
    letter-spacing: 0.3px;
    text-transform: uppercase;
    text-align: right;
  }
  .person { position: absolute; left: 32px; top: 194px; }
  .person-name {
    font-weight: 600;
    font-size: 26px;
    text-transform: uppercase;
    line-height: 1.05;
  }
  .person-title { font-weight: 400; font-size: 18px; line-height: 1.2; }
  .divider {
    position: absolute; left: 32px; top: 259px;
    width: 24px; height: 1.5px; background: var(--navy);
  }
  .contact-list { position: absolute; left: 32px; top: 278px; list-style: none; }
  .contact-item {
    display: flex; align-items: center; gap: 8px;
    font-size: 16px; height: 26.5px; letter-spacing: 0.3px;
  }
  .contact-icon { width: 13px; height: 13px; fill: var(--navy); flex: none; }

  /* Back */
  .back-brand {
    position: absolute; left: 0; right: 0; top: 160px;
    display: flex; flex-direction: column; align-items: center;
  }
  .back-row { display: flex; align-items: center; gap: 14px; }
  .brand-square { width: 38px; height: 38px; background: var(--accent-orange); }
  .back-brand .brand-name { font-size: 58px; }
  .back-brand .brand-tagline {
    align-self: flex-end; margin-right: 146px; font-size: 8px; margin-top: 6px;
  }
</style>
</head>
<body>
<main class="canvas">
  <section class="card card-front">
    <div class="front-brand">
      <div class="brand-name">Brightwell Labs</div>
      <div class="brand-tagline">A division of Brightwell Civic</div>
    </div>
    <div class="person">
      <div class="person-name">Martin Quelbrook</div>
      <div class="person-title">CEO</div>
    </div>
    <div class="divider"></div>
    <ul class="contact-list">
      <li class="contact-item">
        <svg class="contact-icon" viewBox="0 0 24 24"><path d="M6.6 10.8a15.1 15.1 0 0 0 6.6 6.6l2.2-2.2a1 1 0 0 1 1-.25 11.4 11.4 0 0 0 3.6.57 1 1 0 0 1 1 1V20a1 1 0 0 1-1 1A17 17 0 0 1 3 4a1 1 0 0 1 1-1h3.5a1 1 0 0 1 1 1c0 1.25.2 2.45.57 3.57a1 1 0 0 1-.25 1z"/></svg>
        555-218-9403
      </li>
      <li class="contact-item">
        <svg class="contact-icon" viewBox="0 0 24 24"><path d="M2 5h20v2l-10 6L2 7z M2 9l10 6 10-6v10H2z"/></svg>
        martin@brightwellcivic.example
      </li>
      <li class="contact-item">
        <svg class="contact-icon" viewBox="0 0 24 24" fill="none" stroke="#2f3a52" stroke-width="1.8"><circle cx="12" cy="12" r="10"/><ellipse cx="12" cy="12" rx="4.5" ry="10"/><path d="M2 12h20M4 7h16M4 17h16"/></svg>
        www.brightwellcivic.example
      </li>
    </ul>
  </section>

  <section class="card card-back">
    <div class="back-brand">
      <div class="back-row">
        <div class="brand-square"></div>
        <div class="brand-name">Brightwell Labs</div>
      </div>
      <div class="brand-tagline">A division of Brightwell Civic</div>
    </div>
  </section>
</main>
</body>
</html>
```